Flowmark Engineering Business Card

our company has just rebranded and taken on a new logo design. We now need to update our business cards with the new logo. This is also an opportunity to reformat and modernize our look. We are an engineering company so the look needs to be formal and professional yet it should look modern. Have a look at our current card and the new card should have the same information.

Target Market(s)

Engineering firms, government, mining companies

Industry/Entity Type

Mechanical Engineering

Contact Information for Business Card

see example attached

Requirements
Must have
• look professional and modern
Should not have
• should not include the office locations 'Brisbane, Sydney and Kuala Lumpur'
• you will find this on the example but it should not be included in these versions. please remove from your submissions and resubmit

```html
<!DOCTYPE html>
<html lang="en">
<head>
<meta charset="utf-8">
<title>Flowmark Engineering – Business Card</title>
<link rel="stylesheet" href="https://fonts.googleapis.com/css2?family=Exo+2:wght@400;500;600&display=swap">
<style>
  :root {
    --brand-blue: #3a4ea0;
    --edge-grey: #cfd1d6;
    --card-white: #f7f7f8;
    --ink: #2e2f33;
    --ink-soft: #55575d;
    --backdrop: #e6e7ea;
  }
  * { margin: 0; padding: 0; box-sizing: border-box; }
  html, body {
    width: 1200px; height: 895px; overflow: hidden;
    background: var(--backdrop);
    font-family: "Exo 2", "Arial", sans-serif;
  }
  .sheet { position: relative; width: 1200px; height: 895px; }
  .card {
    position: absolute; left: 250px; width: 700px; height: 400px;
    background: var(--card-white);
    box-shadow: 0 6px 18px rgba(0,0,0,.18);
    overflow: hidden;
  }
  .card--front { top: 30px; }
  .card--back { top: 465px; }
  .card__bands { position: absolute; inset: 0; }
  .brand {
    position: absolute; display: flex; align-items: center; gap: 14px;
    color: var(--brand-blue); font-weight: 600; letter-spacing: 2px;
    text-transform: uppercase;
  }
  .brand__dot {
    width: 46px; height: 46px; border-radius: 50%;
    background: var(--brand-blue); flex: none;
  }
  .card--front .brand { left: 36px; top: 38px; font-size: 30px; }
  .card--back .brand {
    left: 0; right: 0; top: 172px; justify-content: center; font-size: 32px;
  }
  .person { position: absolute; left: 470px; top: 100px; color: var(--ink); }
  .person__name { font-size: 26px; font-weight: 500; letter-spacing: 2px; text-transform: uppercase; }
  .person__role { font-size: 11px; letter-spacing: 1.5px; margin-top: 6px; color: var(--ink-soft); text-transform: uppercase; }
  .contact { position: absolute; color: var(--ink); font-size: 15px; line-height: 1.45; letter-spacing: .5px; }
  .contact--web { left: 30px; top: 178px; }
  .contact--address { left: 258px; top: 226px; }
  .contact--phone { left: 478px; top: 278px; font-size: 17px; letter-spacing: 1.5px; }
</style>
</head>
<body>
<main class="sheet">

  <section class="card card--front" aria-label="Business card front">
    <svg class="card__bands" viewBox="0 0 700 400" aria-hidden="true">
      <!-- stepped chevron bar -->
      <polygon fill="var(--brand-blue)" points="0,120 210,120 226,140 210,160 0,160"/>
      <polygon fill="var(--brand-blue)" points="232,170 430,170 446,190 430,210 232,210 248,190"/>
      <polygon fill="var(--brand-blue)" points="452,220 700,220 700,260 452,260 468,240"/>
      <polyline fill="none" stroke="var(--edge-grey)" stroke-width="4" points="216,160 234,140 216,120"/>
      <polyline fill="none" stroke="var(--edge-grey)" stroke-width="4" points="436,210 454,190 436,170"/>
      <!-- bottom band -->
      <rect x="0" y="338" width="700" height="12" fill="var(--edge-grey)"/>
      <rect x="0" y="350" width="700" height="50" fill="var(--brand-blue)"/>
      <!-- globe icon -->
      <g fill="none" stroke="#fff" stroke-width="2">
        <circle cx="48" cy="140" r="12"/>
        <ellipse cx="48" cy="140" rx="5" ry="12"/>
        <line x1="36" y1="140" x2="60" y2="140"/>
        <line x1="38" y1="133" x2="58" y2="133"/>
        <line x1="38" y1="147" x2="58" y2="147"/>
      </g>
      <!-- pin icon -->
      <path fill="#fff" d="M338,178 a10,10 0 0 1 10,10 c0,8 -10,16 -10,16 c0,0 -10,-8 -10,-16 a10,10 0 0 1 10,-10 z"/>
      <circle cx="338" cy="188" r="3.5" fill="var(--brand-blue)"/>
      <!-- phone icon -->
      <g fill="none" stroke="#fff" stroke-width="2">
        <rect x="636" y="226" width="16" height="28" rx="3"/>
        <line x1="641" y1="249" x2="647" y2="249"/>
      </g>
    </svg>

    <div class="brand"><span class="brand__dot"></span>Flowmark Engineering</div>

    <div class="person">
      <p class="person__name">Daniel Reeve</p>
      <p class="person__role">Graphics Designer</p>
    </div>

    <p class="contact contact--web">hello@flowmarkmail.com<br>www.flowmarkeng.net</p>
    <p class="contact contact--address">217, 9th floor, Quay<br>Harbour Lane NTX</p>
    <p class="contact contact--phone">012 555 0142<br>012 555 0142</p>
  </section>

  <section class="card card--back" aria-label="Business card back">
    <svg class="card__bands" viewBox="0 0 700 400" aria-hidden="true">
      <polygon fill="var(--brand-blue)" points="0,0 230,0 230,40 0,40"/>
      <polygon fill="var(--brand-blue)" points="236,0 470,0 470,62 236,62 250,31"/>
      <polygon fill="var(--brand-blue)" points="476,0 700,0 700,40 476,40 490,20"/>
      <polygon fill="var(--brand-blue)" points="0,360 210,360 210,400 0,400"/>
      <polygon fill="var(--brand-blue)" points="216,338 450,338 450,400 216,400 230,369"/>
      <polygon fill="var(--brand-blue)" points="456,360 700,360 700,400 456,400 470,380"/>
    </svg>
    <div class="brand"><span class="brand__dot"></span>Flowmark Engineering</div>
  </section>

</main>
</body>
</html>
```